Broschüren-Design für Unternehmen, das die Begrünung von Bürogebäuden anbietet
Wir sind mit der Zusammenarbeit mit inkmolde äußerst zufrieden. Vielen Dank für das ganze Mitdenken und die wichtigen Rückfragen an uns (Format, Layout, Farben, Papierwahl)! :)
Zielgruppe
Unser Kerngeschäft besteht in der Begrünung von Bürogebäuden.
Das heißt, wir liefern und pflegen exotische und tropische immergrüne Planzen für zum Beispiel Eingangsbereiche, Atrien, sowie Einzel- und Großraumbüros.
Die Zielgruppe besteht fast ausschließlich aus gewerblichen Kunden.
Aufgabenstellung
Die Vorlage ist ein grober Entwurf und Vorschlag von uns. Es darf davon auch gerne abgewichen werden.
Die Broschüre soll uns als Unterstützung für Erstgespräche bei potentiellen Neukunden dienen und verbleibt beim Kunden. Sie soll unsere Firma, uns als Menschen und unsere Produkte und Dienstleistung kurz präsentieren und einen guten Eindruck hinterlassen.
Danach wünschen wir uns idealerweise eine Kontaktaufnahme durch den Kunden selbst.

```html
<!DOCTYPE html>
<html lang="de">
<head>
<meta charset="utf-8">
<title>Broschüre Innenraumbegrünung</title>
<link rel="stylesheet" href="https://fonts.googleapis.com/css2?family=Alegreya+Sans:ital,wght@0,400;0,500;1,700;1,800&display=swap">
<style>
:root{
  --paper:#ffffff;
  --stone:#e9e5e2;
  --ink:#1d1d1b;
  --mark:#ffffff;
}
*{margin:0;padding:0;box-sizing:border-box}
html,body{width:1200px;height:566px;overflow:hidden;background:var(--paper)}
body{font-family:"Alegreya Sans",sans-serif;color:var(--ink)}
.spread{position:relative;width:1200px;height:566px;background:var(--paper)}
.block{position:absolute}
.photo{position:absolute}
.photo-atrium-tree{left:0;top:0;width:235px;height:566px;background:linear-gradient(170deg,#f4f1e6 0%,#a9c57c 30%,#5f8a3d 55%,#7a5b44 80%,#5c4b40 100%)}
.photo-rubber-plant{left:235px;top:0;width:164px;height:102px;background:linear-gradient(180deg,#c9d3d4 0%,#3f6a3a 55%,#c84a50 100%)}
.photo-bonsai{left:235px;top:104px;width:164px;height:106px;background:linear-gradient(180deg,#cfd8d9 0%,#7f9a56 50%,#c84a50 100%)}
.photo-palm{left:588px;top:0;width:212px;height:370px;background:linear-gradient(180deg,#eef0ee 0%,#5f8468 40%,#9aa3a0 75%,#d9d2c8 100%)}
.photo-planter-bed{left:235px;top:370px;width:244px;height:196px;background:linear-gradient(160deg,#eaeee6 0%,#6d9650 40%,#2f5a2a 75%,#8a5a44 100%)}
.photo-moss-wall{left:800px;top:133px;width:400px;height:433px;background:linear-gradient(100deg,#4e5a24 0%,#b8a67a 30%,#6f7a2e 50%,#a59570 70%,#5a4a3a 100%)}

.panel-stone{background:var(--stone)}
.panel-quote{left:235px;top:210px;width:353px;height:160px}
.panel-top-right{left:800px;top:0;width:400px;height:133px}

.headline{font-weight:800;font-style:italic;font-size:18px;line-height:22px;letter-spacing:.1px}
.quote{left:254px;top:225px;width:170px;font-weight:800;font-style:italic;font-size:20px;line-height:26px;white-space:nowrap}
.copy{font-size:7.4px;line-height:8.75px}
.justified{text-align:justify;hyphens:manual}

.care{left:424px;top:28px;width:145px}
.care .headline{margin-bottom:25px}
.care .copy p+p{margin-top:8.5px}
.quote-copy{left:424px;top:232px;width:146px}
.quote-copy p+p{margin-top:1.5px}
.new-green{left:502px;top:398px;width:274px}
.new-green .headline{margin-bottom:19px}
.new-green .copy p+p{margin-top:3.5px}
.new-green .copy .spacer{margin-top:20px}
.more{left:830px;top:28px;width:262px}
.more .headline{margin-bottom:14px}

.caption{position:absolute;height:17px;background:var(--stone);font-size:4.4px;line-height:5px;display:flex;align-items:center;padding-left:44px}
.caption-oldest{left:0;top:418px;width:125px}
.caption-largest{left:674px;top:324px;width:126px;padding-left:46px}
.caption-bed{left:353px;top:518px;width:126px;padding-left:46px}
.caption-moss{left:1075px;top:524px;width:125px;padding-left:46px}
.dot{position:absolute;top:-6px;width:28px;height:28px;border:2px solid var(--mark);border-radius:50%}
.dot-big{position:absolute;left:1104px;top:28px;width:68px;height:68px;border:3px solid var(--mark);border-radius:50%}
</style>
</head>
<body>
<main class="spread">
  <div class="photo photo-atrium-tree" role="img" aria-label="Foto: großer Gummibaum in einem Atrium einer Eingangshalle"></div>
  <div class="photo photo-rubber-plant" role="img" aria-label="Foto: Gummibaum im roten Pflanzgefäß"></div>
  <div class="photo photo-bonsai" role="img" aria-label="Foto: Zimmertanne im roten Pflanzgefäß"></div>
  <div class="photo photo-palm" role="img" aria-label="Foto: hohe Kentia-Palme in Edelstahlkübel"></div>
  <div class="photo photo-planter-bed" role="img" aria-label="Foto: bepflanztes Beet mit tropischen Grünpflanzen"></div>
  <div class="photo photo-moss-wall" role="img" aria-label="Foto: Café mit Mooswand und Holztischen"></div>

  <div class="block panel-stone panel-quote"></div>
  <div class="block panel-stone panel-top-right"></div>

  <section class="block care">
    <h2 class="headline">Pflege &amp; Wartung<br>Bestandspflanzen</h2>
    <div class="copy justified">
      <p>Sie kommen morgens in die Firma, öffnen die Tür zum Büro, setzen sich, und haben bereits eine Grünpflanze vor sich?</p>
      <p>Hervorragend! Gießen, Düngen, Schneiden, Abstauben, Umtopfen: kurzum die Rundum&shy;versorgung Ihrer Pflanzen bieten wir Ihnen ger&shy;ne für Ihren existierenden kleinen Urwald an.</p>
    </div>
  </section>

  <blockquote class="block quote">„Wir kümmern<br>uns mit unserem<br>Team gerne um<br>Ihre bestehenden<br>Pflanzen.“</blockquote>

  <section class="block quote-copy copy">
    <p>Unsere ältesten Schützlinge wurden in den 1970ern gepflanzt und erfreuen sich auch in ihrem bald 50. Lebensjahr bester Gesundheit. Unsere kleinsten Grünen sind kaum höher als ein Steckling, unsere Größten strecken sich in Eingangshallen bis 5 Meter in die Höhe.</p>
    <p>Manche unserer Kunden erfreuen sich in ihrer Hauptverwaltung an 2000 Pflanzen und das typische Startup ist stolz auf die ersten 5 grünen Mitbewohner. Wir sind spezialisiert auf die Innenraumbegrünung, die wir mögen, können und lieben.</p>
    <p>Vielleicht auch bald in Ihren Räumlichkeiten?</p>
  </section>

  <section class="block new-green">
    <h2 class="headline">Neubegrünung &amp; Lieferung</h2>
    <div class="copy">
      <p>Sie kommen morgens in die Firma, öffnen die Tür zum Büro, setzen sich, und starren erst einmal auf eine kahle Wand?<br>Zeit, etwas Farbe in Ihr Büro zu bringen. Und am besten natürlich grün! Pflanzen im Büro lockern die Arbeitsatmosphäre auf und sorgen dafür, dass sich alle wohlfühlen.</p>
      <p>Wir kümmern uns um die Neubegrünung Ihrer Büroräumlichkeiten.</p>
      <p class="spacer">Platz für weiteren Text … Platz für weiteren Text … Platz für weiteren Text … Platz für weiteren Text … Platz für weiteren Text … Platz für weiteren Text … Platz für weiteren Text … Platz für weiteren Text … Platz für weiteren Text … Platz für weiteren Text … Platz für weiteren Text … Platz für weiteren Text … Platz für weiteren Text … Platz für weiteren Text … Platz für weiteren Text … Platz für weiteren</p>
    </div>
  </section>

  <section class="block more">
    <h2 class="headline">Platz für weiteren Text</h2>
    <p class="copy">Platz für weiteren Text … Platz für weiteren Text … Platz für weiteren Text … Platz für weiteren Text … Platz für weiteren Text … Platz für weiteren Text … Platz für weiteren Text … Platz für weiteren Text … Platz für weiteren Text … Platz für weiteren Text … Platz für weiteren Text … Platz für weiteren Text … Platz für weiteren Text … Platz für weiteren Text … Platz für weiteren Text … Platz für weiteren</p>
  </section>

  <span class="dot-big" aria-hidden="true"></span>

  <div class="caption caption-oldest">
    <span class="dot" style="left:11px" aria-hidden="true"></span>
    <span>Einer unserer ältesten:<br>Gepflanzt 1978, stolze 41 Jahre alt</span>
  </div>
  <div class="caption caption-largest">
    <span class="dot" style="left:11px" aria-hidden="true"></span>
    <span>Einer unserer größten: 5 Meter</span>
  </div>
  <div class="caption caption-bed">
    <span class="dot" style="left:5px" aria-hidden="true"></span>
    <span>Infos zum Bild</span>
  </div>
  <div class="caption caption-moss">
    <span class="dot" style="left:5px" aria-hidden="true"></span>
    <span>Infos zum Bild</span>
  </div>
</main>
</body>
</html>
```